Satchel & Sundial needs new business card design

I need a new business card design. I'm looking for out-of-the-box design which represents the freedom of being a location independent entrepreneur.
I offer coaching, retreats and trips.
I would like to see designs with and without the photo.
Colors I use are black (#000000), green (#25A796) and brown (#D7C38C)
Website satchelandsundial.example

Target Market(s)

location independent entrepreneurs, digital nomads, people looking to swap the 9 to 5 for a lifestyle business

Industry/Entity Type

Business

Contact Information for Business Card

Dorota Falkner
Your Lifestyle Business Coach, Retreat & Trip Leader
http://satchelandsundial.example
hello@satchelandsundial.example
Live a life you don't need a holiday from

Font styles to use
Serif
Sans Serif

Requirements
Must have
• One side should contain only the logo. I would also consider having the "Live a life you don't need a holiday from" on that side too (depending on how it looks)
• Please show both sides on the designs.

```html
<!DOCTYPE html>
<html lang="en">
<head>
<meta charset="utf-8">
<title>Satchel &amp; Sundial – Business Card</title>
<link rel="stylesheet" href="https://fonts.googleapis.com/css2?family=Oswald:wght@400;500;600&family=Caveat+Brush&display=swap">
<style>
  :root {
    --ink: #141414;
    --teal: #17917f;
    --card: #fbfbfb;
    --backdrop: #e4e4e4;
  }
  * { margin: 0; padding: 0; box-sizing: border-box; }
  html, body {
    width: 1200px;
    height: 576px;
    overflow: hidden;
    background: var(--backdrop);
  }
  .stage {
    position: relative;
    width: 1200px;
    height: 576px;
  }
  .card {
    position: absolute;
    top: 139px;
    width: 484px;
    height: 293px;
    background: var(--card);
    border-radius: 8px;
    overflow: hidden;
  }
  .card--front { left: 82px; }
  .card--back { left: 602px; }

  .brand-name {
    font-family: "Oswald", sans-serif;
    font-weight: 500;
    color: var(--ink);
    text-transform: uppercase;
    letter-spacing: 0.5px;
    white-space: nowrap;
  }
  .card--front .brand-name {
    position: absolute;
    left: 0;
    right: 0;
    top: 120px;
    text-align: center;
    font-size: 36px;
    line-height: 1;
  }
  .card--back .brand-name {
    position: absolute;
    left: 26px;
    top: 30px;
    font-size: 27px;
    line-height: 1;
  }

  .person {
    position: absolute;
    left: 18px;
    top: 160px;
    font-family: "Oswald", sans-serif;
  }
  .person__name {
    font-weight: 600;
    font-size: 17px;
    line-height: 1.2;
    color: var(--ink);
    text-transform: uppercase;
  }
  .person__role {
    font-weight: 400;
    font-size: 11px;
    line-height: 14px;
    color: var(--teal);
    margin-top: 4px;
  }
  .tagline {
    position: absolute;
    left: 18px;
    top: 240px;
    font-family: "Caveat Brush", cursive;
    font-size: 14px;
    color: var(--teal);
  }

  .contact {
    position: absolute;
    left: 284px;
    font-family: "Oswald", sans-serif;
    font-size: 11.5px;
    color: var(--ink);
    display: flex;
    align-items: center;
    gap: 8px;
    white-space: nowrap;
  }
  .contact--email { top: 182px; }
  .contact--web { top: 202px; }
  .contact--social { top: 241px; color: var(--teal); }
  .contact__icon { width: 11px; height: 11px; flex: none; }
  .contact__square {
    width: 10px;
    height: 10px;
    background: var(--ink);
    border-radius: 2px;
    flex: none;
  }

  .footer-band {
    position: absolute;
    left: 0;
    bottom: 4px;
    width: 484px;
    height: 12px;
  }
</style>
</head>
<body>
<main class="stage">

  <section class="card card--front" aria-label="Card front">
    <p class="brand-name">Satchel &amp; Sundial</p>
  </section>

  <section class="card card--back" aria-label="Card back">
    <p class="brand-name">Satchel &amp; Sundial</p>

    <div class="person">
      <p class="person__name">Dorota Falkner</p>
      <p class="person__role">Your Lifestyle Business Coach<br>Retreat &amp; Trip Leader</p>
    </div>

    <p class="tagline">Live a life you don't need a holiday from</p>

    <p class="contact contact--email">
      <svg class="contact__icon" viewBox="0 0 12 12" aria-hidden="true">
        <rect x="0.5" y="2" width="11" height="8" fill="var(--teal)"/>
        <polyline points="0.5,2 6,6.5 11.5,2" fill="none" stroke="#fff" stroke-width="1"/>
      </svg>
      hello@satchelandsundial.example
    </p>
    <p class="contact contact--web">
      <svg class="contact__icon" viewBox="0 0 12 12" aria-hidden="true">
        <circle cx="6" cy="6" r="5.3" fill="var(--teal)"/>
        <ellipse cx="6" cy="6" rx="2.2" ry="5.3" fill="none" stroke="#fff" stroke-width="0.8"/>
        <line x1="0.7" y1="6" x2="11.3" y2="6" stroke="#fff" stroke-width="0.8"/>
      </svg>
      www.satchelandsundial.example
    </p>
    <p class="contact contact--social">
      <span class="contact__square" aria-hidden="true"></span>
      /satchelandsundial
    </p>

    <svg class="footer-band" viewBox="0 0 484 12" preserveAspectRatio="none" aria-hidden="true">
      <polygon points="0,12 0,0 324,0 316,12" fill="var(--teal)"/>
      <polygon points="324,0 330,0 322,12 316,12" fill="#fff"/>
      <polygon points="330,0 484,0 484,12 322,12" fill="var(--ink)"/>
    </svg>
  </section>

</main>
</body>
</html>
```